Brookvale Building Company - advertisement poster

I am looking to print some canvas signs to advertise my general contracting company, Brookvale Building Company. The sign will measure 6' long x 3' high so the size should match that ratio. I already have a logo icon, which is the Letter 'B' and some trees that I would like to incorporate, see attached. I would also like the to have the following information listed:
1) phone number: 831-555-0172
2) email: brookvalebuildingcompany@mailnest.example
3) website: brookvalebuildingcompany.example
4) Lic#4826130
5) I want to use this text: "BUILD WITH THE B-CREW!"

The ad should be relatively simple and clean. Black and Green are my company colors. I am open to creative ideas!

Target Market(s)

People looking to renovate their homes

Industry/Entity Type

Construction

Colors
59FF00
82FF00
B8FF75
E3FFCB
F4FFEA

Requirements
Must have
• Must have my company logo
Should not have
• No photos or complex graphics

```html
<!DOCTYPE html>
<html lang="en">
<head>
<meta charset="utf-8">
<title>Brookvale Building Company – Sign</title>
<link rel="stylesheet" href="https://fonts.googleapis.com/css2?family=Fira+Sans+Condensed:wght@700;800&family=Jost:wght@400;700&display=swap">
<style>
  :root {
    --bg: #f4faea;
    --navy: #242162;
    --green-deep: #69b04a;
    --green-mid: #7dc242;
    --green-lime: #96c93d;
    --green-pale: #bfdb6f;
    --grey: #8a8a8a;
  }
  html, body {
    margin: 0;
    padding: 0;
    overflow: hidden;
    background: var(--bg);
  }
  .sign {
    position: relative;
    width: 1200px;
    height: 600px;
    background: var(--bg);
    overflow: hidden;
  }
  .forest {
    position: absolute;
    left: 0;
    top: 0;
    width: 1200px;
    height: 600px;
  }
  .brand {
    position: absolute;
    left: 730px;
    top: 40px;
    width: 408px;
    height: 260px;
    display: flex;
    align-items: center;
    justify-content: center;
    gap: 18px;
  }
  .brand-mark {
    width: 48px;
    height: 48px;
    flex: none;
    background: var(--navy);
  }
  .brand-name {
    margin: 0;
    font-family: "Jost", sans-serif;
    font-weight: 700;
    font-size: 44px;
    line-height: 1.05;
    color: var(--navy);
    text-transform: uppercase;
    letter-spacing: 1px;
  }
  .headline {
    position: absolute;
    left: 420px;
    top: 330px;
    width: 722px;
    margin: 0;
    font-family: "Fira Sans Condensed", sans-serif;
    font-weight: 800;
    font-size: 76px;
    line-height: 1;
    color: var(--navy);
    white-space: nowrap;
    text-align: center;
  }
  .contact {
    position: absolute;
    left: 760px;
    top: 0;
    width: 386px;
    height: 600px;
    text-align: center;
  }
  .contact p {
    position: absolute;
    left: 0;
    width: 100%;
    margin: 0;
    white-space: nowrap;
  }
  .contact-phone {
    top: 440px;
    font-family: "Fira Sans Condensed", sans-serif;
    font-weight: 700;
    font-size: 37px;
    line-height: 40px;
    color: var(--green-deep);
  }
  .contact-line {
    font-family: "Jost", sans-serif;
    font-weight: 400;
    font-size: 17px;
    line-height: 24px;
    color: var(--green-mid);
  }
  .contact-email { top: 489px; }
  .contact-web { top: 518px; }
  .license {
    top: 559px;
    font-family: "Jost", sans-serif;
    font-weight: 400;
    font-size: 17px;
    line-height: 24px;
    color: var(--grey);
  }
</style>
</head>
<body>
  <main class="sign">
    <svg class="forest" viewBox="0 0 1200 600" role="img" aria-label="Overlapping stylised pine trees in several shades of green forming a forest along the left side">
      <defs>
        <linearGradient id="forest-tone" x1="0" y1="0" x2="1" y2="1">
          <stop offset="0" stop-color="#7dc242"/>
          <stop offset="0.45" stop-color="#96c93d"/>
          <stop offset="1" stop-color="#69b04a"/>
        </linearGradient>
      </defs>
      <polygon fill="url(#forest-tone)" points="0,0 530,0 725,497 665,600 0,600"/>
    </svg>

    <header class="brand">
      <span class="brand-mark" aria-hidden="true"></span>
      <h1 class="brand-name">Brookvale<br>Building Company</h1>
    </header>

    <p class="headline">Build with the B-Crew!</p>

    <section class="contact">
      <p class="contact-phone">831 555 0172</p>
      <p class="contact-line contact-email">brookvalebuildingcompany@mailnest.example</p>
      <p class="contact-line contact-web">brookvalebuildingcompany.example</p>
      <p class="license">Lic# 4826130</p>
    </section>
  </main>
</body>
</html>
```